Corvana Tongue Works, LLC

We need a business card that includes information about our business and conveys a reliable business that provides document translation services and interpreters for a variety of corporate and individual clients. We want to come across as professional, reliable, yet approachable. It should include the following on one side:

ESL / ENL Language Classes, Private Lessons, and Online Tutors
PLEXA Training and Testing
Translating & Interpreting Services
Contact us about Over-the-Phone Interpreting in over 200 languages
24/7/365
www.corvanatongue.example

The other side should include (555) 481-3062

Rhoda Pelling, President
482 Garnet Ave., Ste. 219
Indianapolis, IN 40917

Please add USA as part of the address. Also, please add rmpelling@corvanatongueworks.example as the e-mail address. Thank you.

Target Market(s)

Business professionals, their families, the international community

Industry/Entity Type

Business

Contact Information for Business Card

24/7/365
www.corvanatongue.example

(555) 481-3062

Rhoda Pelling, President
482 Garnet Ave., Ste. 219
Indianapolis, IN 40917
USA

Font styles to use
Sans Serif

Colors

Designer to choose colors to be used in the design.

Requirements
Must have
• See project description
• e-mail address and web address
• Phone number
Nice to have
• a globe
• physical address
Should not have
• Should not have the same color scheme as other agencies in our market in Indiana unless it is blue and black. No purple or yellow.

```html
<!DOCTYPE html>
<html lang="en">
<head>
<meta charset="utf-8">
<title>Corvana Tongue Works – Business Card</title>
<link href="https://fonts.googleapis.com/css2?family=Lato:wght@400;700&display=swap" rel="stylesheet">
<style>
  :root {
    --stage: #9a9a9a;
    --card-white: #ffffff;
    --brand-blue: #2196d6;
    --ink: #161616;
    --band-black: #000000;
    --rule-grey: #b9b9b9;
    --on-blue: #ffffff;
  }
  * { margin: 0; padding: 0; box-sizing: border-box; }
  html, body {
    width: 1200px; height: 900px; overflow: hidden;
    background: var(--stage);
    font-family: "Lato", Arial, sans-serif;
    color: var(--ink);
  }
  .stage { position: relative; width: 1200px; height: 900px; }

  .card {
    position: absolute; top: 306px; width: 438px; height: 271px;
    border-radius: 10px; overflow: hidden;
    box-shadow: 2px 3px 6px rgba(0,0,0,0.35);
  }
  .card-front { left: 150px; background: var(--card-white); }
  .card-back { left: 610px; background: var(--brand-blue); }

  /* Front */
  .brand-mark {
    position: absolute; left: 20px; top: 102px;
    width: 68px; height: 68px; border-radius: 50%;
    background: var(--brand-blue);
  }
  .brand-name {
    position: absolute; left: 96px; top: 104px;
    font-size: 18px; line-height: 21px; font-weight: 400;
    color: var(--ink); white-space: nowrap;
  }
  .front-divider {
    position: absolute; left: 200px; top: 76px;
    width: 1px; height: 122px; background: var(--rule-grey);
  }
  .contact { position: absolute; left: 210px; top: 72px; white-space: nowrap; }
  .contact-name {
    font-size: 17px; font-weight: 700; color: var(--brand-blue);
    letter-spacing: 0.2px; line-height: 20px;
  }
  .contact-title { font-size: 11.5px; line-height: 16px; margin-bottom: 6px; }
  .contact-line {
    display: flex; align-items: center; gap: 4px;
    font-size: 11px; line-height: 17px;
  }
  .contact-line svg { width: 13px; height: 13px; flex: none; }
  .contact-address { font-size: 11px; line-height: 16px; margin-top: 4px; }

  /* Back */
  .back-brand {
    position: absolute; left: 48px; top: 96px; width: 140px;
    text-align: center; color: var(--on-blue);
    font-size: 18px; line-height: 22px; font-weight: 700;
  }
  .back-divider {
    position: absolute; left: 194px; top: 74px;
    width: 1px; height: 88px; background: var(--on-blue);
  }
  .services {
    position: absolute; left: 212px; top: 70px;
    list-style: none; color: var(--on-blue);
    font-size: 12px; line-height: 15.5px;
  }
  .services li { position: relative; padding-left: 12px; }
  .services li::before {
    content: ""; position: absolute; left: 1px; top: 5px;
    width: 5px; height: 5px; border-radius: 50%; background: var(--on-blue);
  }
  .availability-band {
    position: absolute; left: 0; bottom: 0; width: 100%; height: 75px;
    background: var(--band-black); color: var(--on-blue);
    text-align: center; font-size: 18px; line-height: 24px;
    padding-top: 10px;
  }
</style>
</head>
<body>
<main class="stage">
  <section class="card card-front" aria-label="Business card front">
    <div class="brand-mark" aria-hidden="true"></div>
    <div class="brand-name">Corvana<br>Tongue<br>Works, LLC</div>
    <div class="front-divider"></div>
    <div class="contact">
      <p class="contact-name">RHODA PELLING</p>
      <p class="contact-title">President</p>
      <p class="contact-line">
        <svg viewBox="0 0 14 14" aria-hidden="true"><circle cx="7" cy="7" r="7" fill="#2196d6"/><path d="M4.2 5.6c0-.9.7-1.3 1.3-1.4l.6 1.4-.7.5c.4.9 1 1.5 1.9 1.9l.5-.7 1.4.6c-.1.6-.5 1.3-1.4 1.3C6 9.2 4.2 7.4 4.2 5.6z" fill="#fff"/></svg>
        (555) 481-3062
      </p>
      <p class="contact-line">
        <svg viewBox="0 0 14 14" aria-hidden="true"><circle cx="7" cy="7" r="7" fill="#2196d6"/><g fill="none" stroke="#fff" stroke-width="0.9"><rect x="3.6" y="4.6" width="6.8" height="4.8" rx="0.5"/><path d="M3.8 4.9 7 7.4l3.2-2.5"/></g></svg>
        rmpelling@corvanatongueworks.example
      </p>
      <p class="contact-line">
        <svg viewBox="0 0 14 14" aria-hidden="true"><circle cx="7" cy="7" r="7" fill="#2196d6"/><g fill="none" stroke="#fff" stroke-width="0.9"><circle cx="7" cy="7" r="3.6"/><ellipse cx="7" cy="7" rx="1.6" ry="3.6"/><path d="M3.4 7h7.2"/></g></svg>
        www.corvanatongue.example
      </p>
      <p class="contact-address">482 Garnet Ave., Ste. 219<br>Indianapolis, IN 40917 USA</p>
    </div>
  </section>

  <section class="card card-back" aria-label="Business card back">
    <div class="back-brand">Corvana<br>Tongue<br>Works</div>
    <div class="back-divider"></div>
    <ul class="services">
      <li>ESL / ENL Language Classes,<br>Private Lessons, and Online Tutors</li>
      <li>PLEXA Training and Testing</li>
      <li>Translating &amp; Interpreting Services</li>
      <li>Contact us about Over-the-Phone<br>Interpreting in over 200 languages</li>
    </ul>
    <div class="availability-band">
      <p>24/7/365</p>
      <p>www.corvanatongue.example</p>
    </div>
  </section>
</main>
</body>
</html>
```